Veranix - Solution provider in business consulting

Veranix is a swiss based company providing solutions for developing markets. The business covers various fields of business consulting, such as supply chain, product costs, quality management and manufacturing management. The Business operates in a efficient, straight and solution oriented manner.
The final design should communicate these characteristics. Asian people as well as as western people shall identify the qualities of the company at first sight.
The customer needs business cards with a simple view but an recognizable design, printed in high quality. Engraved elements such as the globe or simple words are possible.
Available colors are: (RAL)
102/102/102
51/102/102
153/204/153
255/102/51
Font: Calibri

```html
<!DOCTYPE html>
<html lang="en">
<head>
<meta charset="utf-8">
<title>Veranix business cards</title>
<link href="https://fonts.googleapis.com/css2?family=Carlito:wght@400;700&display=swap" rel="stylesheet">
<style>
  :root {
    --stage: #e9e7e3;
    --card-back: #a6a6a6;
    --panel-dark: #666666;
    --panel-edge: #8a8a8a;
    --paper: #ffffff;
    --ink-light: #ffffff;
    --ink-soft: #e4e4e4;
    --brand-grey: #666666;
    --shadow: rgba(0, 0, 0, 0.28);
  }
  * { box-sizing: border-box; margin: 0; padding: 0; }
  html, body {
    width: 1200px; height: 950px; overflow: hidden;
    background: var(--stage);
    font-family: "Carlito", sans-serif;
  }
  .canvas { position: relative; width: 1200px; height: 950px; }

  .card {
    position: absolute; width: 620px; height: 400px;
    box-shadow: 0 14px 30px var(--shadow);
    overflow: hidden;
  }

  /* Back side */
  .card--back {
    left: 120px; top: 50px;
    background: var(--card-back);
    display: flex; flex-direction: column; align-items: center; justify-content: center;
  }
  .brand {
    display: flex; align-items: center; gap: 14px;
    font-weight: 400; letter-spacing: 1px;
  }
  .brand__dot { width: 30px; height: 30px; border-radius: 50%; }
  .card--back .brand { color: var(--ink-light); font-size: 60px; }
  .card--back .brand__dot { background: var(--ink-light); }
  .card--back .web {
    margin-top: 34px; color: var(--ink-light);
    font-size: 17px; letter-spacing: 5px;
  }

  /* Front side */
  .card--front {
    left: 460px; top: 500px;
    display: flex; background: var(--paper);
  }
  .contact-panel {
    width: 47%; height: 100%;
    background: var(--panel-dark);
    border-right: 6px solid var(--panel-edge);
    padding: 46px 30px 30px 38px;
    color: var(--ink-light);
    display: flex; flex-direction: column;
  }
  .person__name { font-weight: 700; font-size: 26px; }
  .person__role { font-size: 17px; margin-top: 2px; margin-left: 10px; color: var(--ink-soft); }
  .company { margin-top: 70px; font-size: 16px; line-height: 1.3; }
  .company__name { font-weight: 700; }
  .contact-list { list-style: none; margin-top: 6px; font-size: 16px; line-height: 1.35; }
  .contact-list li { display: flex; align-items: center; gap: 10px; }
  .contact-list svg { width: 14px; height: 14px; flex: none; }
  .logo-panel {
    flex: 1; display: flex; align-items: center; justify-content: center;
  }
  .card--front .brand { color: var(--brand-grey); font-size: 52px; }
  .card--front .brand__dot { background: var(--brand-grey); width: 26px; height: 26px; }
</style>
</head>
<body>
<main class="canvas">
  <section class="card card--back" aria-label="Card back">
    <div class="brand"><span class="brand__dot"></span><span class="brand__name">veranix</span></div>
    <p class="web">www.veranix.ch</p>
  </section>

  <section class="card card--front" aria-label="Card front">
    <div class="contact-panel">
      <h1 class="person__name">Marco Keller</h1>
      <p class="person__role">CEO</p>
      <div class="company">
        <p class="company__name">Veranix GmbH</p>
        <p>Talstrasse 8, 9200 Gossau</p>
        <p>Switzerland</p>
      </div>
      <ul class="contact-list">
        <li>
          <svg viewBox="0 0 16 16" aria-hidden="true"><path fill="#fff" d="M2 4c0-1 1-2 2-2h8c1 0 2 1 2 2v1h-3V4H5v1H2z M4 7h8l2 6H2z"/><circle cx="8" cy="10" r="1.6" fill="#666"/></svg>
          +41 71 555 0182
        </li>
        <li>
          <svg viewBox="0 0 16 16" aria-hidden="true"><rect x="4" y="1" width="8" height="14" rx="1.5" fill="none" stroke="#fff" stroke-width="1.6"/><circle cx="8" cy="12.5" r="0.9" fill="#fff"/></svg>
          +41 79 555 0347
        </li>
        <li>
          <svg viewBox="0 0 16 16" aria-hidden="true"><rect x="1" y="3.5" width="14" height="9" fill="#fff"/><path d="M1 3.5l7 5 7-5" fill="none" stroke="#666" stroke-width="1.2"/></svg>
          marco.keller@veranix.ch
        </li>
        <li>
          <svg viewBox="0 0 16 16" aria-hidden="true"><circle cx="8" cy="8" r="7" fill="#fff"/><path d="M1 8h14M8 1c-3 3-3 11 0 14M8 1c3 3 3 11 0 14" fill="none" stroke="#666" stroke-width="1"/></svg>
          www.veranix.ch
        </li>
      </ul>
    </div>
    <div class="logo-panel">
      <div class="brand"><span class="brand__name">veranix</span><span class="brand__dot"></span></div>
    </div>
  </section>
</main>
</body>
</html>
```